BOLD & MINIMALIST DESIGN NEEDED

We want a very bold but minimalistic business card design that is impactful and utilizes both sides of the business card. Our current logo is included for your use.

We want bold fonts and good use of negative space. We don't want the logo to overpower the design.

Target Market(s)

Professionals who are building new commercial buildings.

Industry/Entity Type

Construction

Contact Information for Business Card

Name, Title, email, office phone, cell phone, website

Font styles to use
Serif
Sans Serif

Requirements
Must have
• Bold design!

```html
<!DOCTYPE html>
<html lang="en">
<head>
<meta charset="utf-8">
<title>Summitcrest Business Card</title>
<link rel="stylesheet" href="https://fonts.googleapis.com/css2?family=Roboto:wght@400;500;700&display=swap">
<style>
  :root {
    --backdrop: #e4e4e4;
    --paper: #ffffff;
    --ink: #0d0d0f;
    --ink-soft: #1c1d20;
    --green: #7dc42a;
    --text-grey: #555555;
    --divider: #c9c9c9;
  }
  * { box-sizing: border-box; margin: 0; padding: 0; }
  html, body { width: 1200px; height: 1200px; overflow: hidden; }
  body {
    background: var(--backdrop);
    font-family: "Roboto", Arial, sans-serif;
    position: relative;
  }
  .card {
    position: absolute;
    left: 257px;
    width: 686px;
    height: 392px;
    overflow: hidden;
  }
  .card--front { top: 165px; background: var(--paper); }
  .card--back {
    top: 653px;
    background: linear-gradient(160deg, #0a0a0b 0%, #111214 55%, var(--ink-soft) 100%);
  }

  .brand {
    position: absolute;
    display: flex;
    align-items: center;
    gap: 10px;
    font-weight: 700;
    letter-spacing: 0.5px;
  }
  .brand__square { width: 22px; height: 22px; background: var(--green); }
  .card--front .brand {
    left: 0; width: 351px; top: 168px;
    justify-content: center;
    font-size: 33px; color: var(--ink);
  }
  .card--back .brand {
    left: 0; right: 0; top: 218px;
    justify-content: center;
    font-size: 48px; color: #ffffff;
  }
  .card--back .brand__square { width: 30px; height: 30px; }

  .divider {
    position: absolute;
    left: 351px; top: 100px;
    width: 1px; height: 202px;
    background: var(--divider);
  }
  .contact { position: absolute; left: 380px; top: 112px; color: var(--text-grey); }
  .contact__name { font-size: 21px; font-weight: 500; color: var(--green); line-height: 1.2; }
  .contact__title { font-size: 14px; font-weight: 500; color: var(--ink); margin-top: 4px; }
  .contact__address { font-size: 15.5px; line-height: 19px; margin-top: 16px; }
  .contact__list { list-style: none; margin-top: 18px; font-size: 15.5px; line-height: 19.5px; }
  .contact__list li { display: flex; align-items: center; gap: 10px; }
  .contact__list svg { width: 13px; height: 13px; flex: none; fill: var(--ink); }

  .front-wave { position: absolute; left: 0; bottom: 0; width: 686px; height: 60px; }

  .back-url {
    position: absolute; left: 0; right: 0; top: 303px;
    text-align: center;
    color: #ffffff;
    font-size: 17px;
    letter-spacing: 3.4px;
  }
</style>
</head>
<body>
  <section class="card card--front">
    <div class="brand"><span class="brand__square"></span>SUMMITCREST</div>
    <div class="divider"></div>
    <div class="contact">
      <p class="contact__name">Daniel Hart</p>
      <p class="contact__title">President</p>
      <p class="contact__address">4120 Alder Court<br>Juneau, Alaska 34512</p>
      <ul class="contact__list">
        <li><svg viewBox="0 0 24 24"><path d="M6.6 10.8a15 15 0 0 0 6.6 6.6l2.2-2.2a1 1 0 0 1 1-.25 11.4 11.4 0 0 0 3.6.57 1 1 0 0 1 1 1V20a1 1 0 0 1-1 1A17 17 0 0 1 3 4a1 1 0 0 1 1-1h3.5a1 1 0 0 1 1 1c0 1.25.2 2.45.57 3.57a1 1 0 0 1-.25 1z"/></svg>555-214-7730</li>
        <li><svg viewBox="0 0 24 24"><path d="M2 5h20v14H2z M4 7v1l8 5 8-5V7l-8 5z" fill-rule="evenodd"/></svg>info@summitcrest.com</li>
        <li><svg viewBox="0 0 24 24"><circle cx="12" cy="12" r="10"/></svg>www.summitcrest.com</li>
      </ul>
    </div>
    <svg class="front-wave" viewBox="0 0 686 60" preserveAspectRatio="none" aria-hidden="true">
      <path d="M0 48 Q343 -14 686 48 L686 60 L0 60 Z" fill="var(--green)"/>
      <path d="M0 53 Q343 -4 686 53 L686 60 L0 60 Z" fill="var(--ink)"/>
    </svg>
  </section>

  <section class="card card--back">
    <div class="brand"><span class="brand__square"></span>SUMMITCREST</div>
    <p class="back-url">www.summitcrest.com</p>
  </section>
</body>
</html>
```